"Vine Hollow Excursions" is a top notch Santa Barbara County Wine Tour company.

We provide scenic, boutique and custom wine tours. I need the card to be clean and classy. I will provide our logo. I would like the logo to cover the back side of the card as an option and would like to see a couple color options other then our signature green and gold. I would like to see some creative options and let the designers come up with options.
I need cards for myself and my team. The final design should communicate "An authentic and boutique wine tour experience"
Please use my website for reference www.vinehollowexcursions.example

Target Market(s)

We have a wide range of clients from millennials to baby boomers

Industry/Entity Type

Tour

Contact Information for Business Card

Contact info:
Dale Morton
805-219-6384
info@vinehollowexcursions.example
vinehollowexcursions.example

Colors

Designer to choose colors to be used in the design.

Requirements
Must have
• my logo
Nice to have
• *I would like to have the backside side with the logo and the company statement
• "An authentic and boutique wine tour experience" as an option.
• *I would also like to see what the designers can create!
• *I would like to see an option that incorporates or social: instagram, yelp, trip advisor
Should not have
• I do not want it too busy.

```html
<!DOCTYPE html>
<html lang="en">
<head>
<meta charset="utf-8">
<title>Vine Hollow Excursions — Business Card</title>
<link rel="stylesheet" href="https://fonts.googleapis.com/css2?family=Cinzel:wght@400;600&family=Open+Sans:wght@400;600&display=swap">
<style>
  :root {
    --page: #3a3b3d;
    --green: #1f5b33;
    --green-deep: #17482a;
    --gold: #a98a5c;
    --white: #ffffff;
    --paper: #f7f7f5;
    --ink: #4a4a4a;
    --tile-1: #6b5a4a;
    --tile-2: #4f8a3c;
    --tile-3: #c9352e;
  }
  * { box-sizing: border-box; margin: 0; padding: 0; }
  html, body { width: 1200px; height: 960px; overflow: hidden; }
  body {
    background: var(--page);
    display: flex;
    flex-direction: column;
    align-items: center;
    justify-content: center;
    gap: 32px;
  }
  .card {
    position: relative;
    width: 760px;
    height: 434px;
    overflow: hidden;
    box-shadow: 0 6px 18px rgba(0,0,0,.35);
  }

  /* Back side */
  .card-back { background: var(--green); color: var(--white); }
  .social-tiles {
    position: absolute; top: 30px; right: 32px;
    display: flex; gap: 8px;
  }
  .social-tile { width: 30px; height: 30px; border-radius: 5px; }
  .social-tile.one { background: var(--tile-1); }
  .social-tile.two { background: var(--tile-2); }
  .social-tile.three { background: var(--tile-3); }
  .back-brand {
    position: absolute; left: 0; right: 0; top: 160px;
    text-align: center;
    font-family: "Open Sans", sans-serif; font-weight: 400;
    font-size: 36px; line-height: 1.2;
    color: var(--white);
  }
  .back-tagline {
    position: absolute; left: 0; right: 0; top: 290px;
    text-align: center;
    font-family: "Open Sans", sans-serif; font-size: 19px;
    color: var(--white);
  }

  /* Front side */
  .card-front { background: var(--paper); }
  .front-brand {
    position: absolute; left: 0; right: 0; top: 78px;
    display: flex; align-items: center; justify-content: center; gap: 14px;
  }
  .front-brand-mark { width: 18px; height: 18px; background: var(--green); }
  .front-brand-name {
    font-family: "Open Sans", sans-serif; font-weight: 400;
    font-size: 34px;
    color: var(--green);
  }
  .name-band {
    position: absolute; left: 0; right: 0; top: 190px; height: 120px;
    background: var(--green);
    border-top: 3px solid var(--gold);
    border-bottom: 3px solid var(--gold);
    box-shadow: inset 0 4px 0 var(--green-deep), inset 0 -4px 0 var(--green-deep);
    display: flex; flex-direction: column; align-items: center; justify-content: center;
    gap: 12px;
  }
  .person-name {
    font-family: "Cinzel", serif; font-weight: 400;
    font-size: 32px; letter-spacing: 1px; color: var(--white);
  }
  .contact-line {
    font-family: "Open Sans", sans-serif; font-size: 17px;
    color: var(--white);
  }
  .website {
    position: absolute; left: 0; right: 0; top: 346px;
    text-align: center;
    font-family: "Cinzel", serif; font-weight: 600;
    font-size: 22px; letter-spacing: 1px; color: var(--ink);
  }
</style>
</head>
<body>
  <section class="card card-back" aria-label="Card back">
    <div class="social-tiles">
      <span class="social-tile one"></span>
      <span class="social-tile two"></span>
      <span class="social-tile three"></span>
    </div>
    <h1 class="back-brand">Vine Hollow Excursions</h1>
    <p class="back-tagline">An authentic &amp; boutique wine tour experience</p>
  </section>

  <section class="card card-front" aria-label="Card front">
    <div class="front-brand">
      <span class="front-brand-mark"></span>
      <span class="front-brand-name">Vine Hollow Excursions</span>
    </div>
    <div class="name-band">
      <p class="person-name">Dale Morton</p>
      <p class="contact-line">P. 805-219-6384 &nbsp;E. info@vinehollowexcursions.example</p>
    </div>
    <p class="website">www.vinehollowexcursions.example</p>
  </section>
</body>
</html>
```